Lifecoach needs website design based on a standard Wordpress theme

I need a website for my new lifecoaching business that can be easily implemented in Wordpress, it needs to be compatible with a standard Wordpress theme. So I can place the pictures, texts etc. in a standard theme of Wordpress.

I want the design to be a very good feeling and playfull one, based on my logo.

Target Market(s)

I will coach people to reach their goals and dreams in life.

Industry/Entity Type

Business

Requirements
Must have
• Can be easy implemented in Wordpress.
Nice to have
• Photo's of nature are nice.

```html
<!DOCTYPE html>
<html lang="en">
<head>
<meta charset="utf-8">
<title>Lena Marsh Lifecoach</title>
<link href="https://fonts.googleapis.com/css2?family=Open+Sans:ital,wght@0,400;0,600;1,600;1,700&family=Tinos:ital,wght@1,400;1,700&display=swap" rel="stylesheet">
<style>
:root{
  --navy:#0d4f86;
  --sky:#23b4e6;
  --btn:#2fbde9;
  --text:#666;
  --nav:#444;
  --line:#e3e3e3;
  --white:#fff;
}
*{margin:0;padding:0;box-sizing:border-box}
html,body{width:838px;height:1200px;overflow:hidden;background:var(--white)}
body{position:relative;font-family:"Open Sans",Arial,sans-serif;color:var(--text)}
.abs{position:absolute}
.header{left:0;top:0;width:838px;height:69px}
.brand{left:92px;top:19px;display:flex;align-items:center;gap:8px}
.brand-mark{width:40px;height:40px;border-radius:50%;border:3px solid var(--sky)}
.brand-name{font-size:15px;font-weight:400;color:var(--navy);letter-spacing:.5px;line-height:1.05}
.nav{top:33px;left:407px;display:flex;gap:28px;font-size:10px;color:var(--nav)}
.hero{left:0;top:69px;width:838px;height:441px;
  background:linear-gradient(180deg,#2a3e48 0%,#55676a 30%,#8c8a5e 52%,#5a7434 64%,#667a2c 80%,#86762e 100%)}
.hero-arrow{top:270px;width:40px;height:42px;border-radius:50%;background:rgba(255,255,255,.3)}
.hero-title{left:0;top:320px;width:838px;text-align:center;font-family:"Tinos","Times New Roman",serif;
  font-style:italic;font-weight:700;font-size:28px;line-height:51px;color:var(--white);text-shadow:0 1px 3px rgba(0,0,0,.5)}
.welcome-title{left:0;top:524px;width:838px;text-align:center;font-size:14.5px;color:var(--navy)}
.welcome-text{left:106px;top:554px;width:626px;text-align:center;font-size:8px;line-height:19.6px}
.card-photo{top:651px;width:203px;height:124px}
.photo-a{left:91px;background:linear-gradient(180deg,#1a3c78 0%,#4d78b0 50%,#2b3f66 78%,#101820 100%)}
.photo-b{left:317px;background:linear-gradient(180deg,#1e4a86 0%,#6c97c8 45%,#b9cde2 65%,#2a3038 100%)}
.card-title{top:787px;font-size:13.5px;color:var(--navy);word-spacing:2px}
.card-text{top:813px;width:208px;font-size:7.8px;line-height:16.4px;letter-spacing:-.05px}
.btn{top:892px;width:86px;height:27px;border-radius:3px;background:var(--btn);color:var(--white);
  font-size:11px;display:flex;align-items:center;justify-content:center}
.t-title{left:544px;top:647px;font-size:14.5px;color:var(--navy)}
.quote-mark{font-family:"Tinos",serif;font-size:22px;line-height:22px;color:#555}
.t-text{left:550px;top:678px;width:196px;font-size:7.8px;line-height:17px}
.avatar{left:551px;top:856px;width:56px;height:56px;border-radius:50%;background:radial-gradient(circle,#c9b7a8 0,#8a7060 60%,#3c3430 100%)}
.t-name{left:628px;top:870px;font-style:italic;font-weight:700;font-size:10.5px;color:var(--sky)}
.t-date{left:628px;top:887px;font-style:italic;font-weight:600;font-size:7.5px;color:#333}
.newsletter{left:91px;top:942px;width:654px;height:90px;border:1px solid #ddd;background:linear-gradient(180deg,#fff 0%,#e9e9e9 100%)}
.nl-title{left:100px;top:970px;font-family:"Tinos",serif;font-style:italic;font-size:21px;color:var(--sky)}
.nl-input{left:282px;top:971px;width:321px;height:33px;border:1px solid #c9c9c9;background:var(--white);
  font-family:"Tinos",serif;font-style:italic;font-size:8px;color:#333;padding:12px 10px}
.nl-btn{left:622px;top:972px;width:112px;height:32px;background:var(--btn);color:var(--white);
  font-family:"Tinos",serif;font-style:italic;font-size:10.5px;display:flex;align-items:center;justify-content:center}
.rule{left:40px;top:1072px;width:798px;height:1px;background:var(--line)}
.social{top:1095px;left:352px;display:flex;gap:9px}
.social span{width:20px;height:20px;border-radius:50%}
.footer-nav{left:0;top:1135px;width:838px;text-align:center;font-size:8px;color:#555;word-spacing:1px}
.footer-nav i{font-style:normal;margin:0 13px}
.copyright{left:0;top:1166px;width:838px;text-align:center;font-size:7.5px;color:#555}
</style>
</head>
<body>
<header class="abs header">
  <div class="abs brand"><span class="brand-mark"></span><span class="brand-name">LENA MARSH LIFECOACH</span></div>
  <nav class="abs nav"><span>Home</span><span>About Us</span><span>Services</span><span>Testimonials</span><span>Contact Us</span></nav>
</header>

<section class="abs hero" role="img" aria-label="Nature photo: sunset over a grassy meadow with trees and the sea"></section>
<div class="abs hero-arrow" style="left:24px">
  <svg width="40" height="42" viewBox="0 0 40 42"><path d="M24 12 L15 21 L24 30" fill="none" stroke="#333" stroke-width="3"/></svg>
</div>
<div class="abs hero-arrow" style="left:770px">
  <svg width="40" height="42" viewBox="0 0 40 42"><path d="M16 12 L25 21 L16 30" fill="none" stroke="#333" stroke-width="3"/></svg>
</div>
<h1 class="abs hero-title">Specialize in transition life coaching<br>for personal and professional empowerment</h1>

<h2 class="abs welcome-title" style="font-weight:400">Welcome To Life Coaching</h2>
<p class="abs welcome-text">Lorem ipsum dolor sit amet, consectetur adipisicing elit, sed do eiusmod tempor incididunt ut labore et dolore magna aliqua. Ut enim ad minim veniam, quis nostrud exercitation ullamco laboris nisi ut aliquip ex ea commodo consequat. Duis aute irure dolor in reprehenderit in voluptate velit esse cillum dolore eu fugiat nulla pariatur. Excepteur sint occaecat cupidatat non proident, sunt in culpa qui officia deserunt mollit anim id est laborum.</p>

<div class="abs card-photo photo-a" role="img" aria-label="Photo: silhouette of a person meditating on rocks at sunset by the sea"></div>
<h3 class="abs card-title" style="left:91px;font-weight:400">Personal Coaching</h3>
<p class="abs card-text" style="left:92px">Dolor sit amet conse ctetur adipisicing elit, sed do eiusmod tempor incididunt ut labore et dolore magna aliqua. Ut enim ad minim veniam, quis nostrud exercitation ullamco laboris nisi ut aliquip ex ea</p>
<div class="abs btn" style="left:91px">Read More</div>

<div class="abs card-photo photo-b" role="img" aria-label="Photo: silhouette of one climber helping another up a rock"></div>
<h3 class="abs card-title" style="left:317px;font-weight:400">Professional Coaching</h3>
<p class="abs card-text" style="left:318px">Dolor sit amet conse ctetur adipisicing elit, sed do eiusmod tempor incididunt ut labore et dolore magna aliqua. Ut enim ad minim veniam, quis nostrud exercitation ullamco laboris nisi ut aliquip ex ea</p>
<div class="abs btn" style="left:317px">Read More</div>

<h3 class="abs t-title" style="font-weight:400">Testimonials</h3>
<span class="abs quote-mark" style="left:529px;top:673px">&lsquo;&lsquo;</span>
<p class="abs t-text">Lorem ipsum dolor sit amet, consectetur adipisicing elit, sed do eiusmod tempor incididunt ut labore et dolore magna aliqua. Ut enim ad minim veniam, quis nostrud exercitation ullamco laboris nisi ut aliquip ex ea commodo consequat. Duis aute irure dolor in reprehenderit in voluptate velit esse cillum dolore eu fugiat nulla pariatur. Excepteur sint occaecat cupidatat non proident, sunt in nt mollit anim id est laborum.</p>
<span class="abs quote-mark" style="left:673px;top:830px">&rsquo;&rsquo;</span>
<div class="abs avatar" role="img" aria-label="Portrait photo of the client giving the testimonial"></div>
<div class="abs t-name">Daniel Brooks</div>
<div class="abs t-date">Posed on 27 mar 2014</div>

<div class="abs newsletter"></div>
<div class="abs nl-title">Newsletter Sign up :</div>
<div class="abs nl-input">Enter Your Email ID :</div>
<div class="abs nl-btn">SUBSCRIBE</div>

<div class="abs rule"></div>
<div class="abs social">
  <span style="background:#1f5fae"></span>
  <span style="background:#333"></span>
  <span style="background:#1d7aa1"></span>
  <span style="background:#e0262e"></span>
  <span style="background:#f0a21f"></span>
</div>
<nav class="abs footer-nav">Home<i>\</i>About Us<i>\</i>Services<i>\</i>Testimonials<i>\</i>Contact Us</nav>
<p class="abs copyright">Copyright 2014Coaching Company.All Right Reseved.</p>
</body>
</html>
```